International Clinical Software Company needs a new business card design

We are looking for a new business card design for our company that has recently expanded into the UK market, making us a multinational company.
After having rebranded our website and produced a new style guide, we are looking for a business card that is creative and attention grabbing, while being consistent with the style and colour scheme used on the new website, www.plumvora.example
We produce care management technology for the aged care market, but the main aspect we aim to communicate is the human element of our software, and the way it assists in providing better care for aged people, and stronger relationships between aged people and the staff that care for them.
Our current business card is a dark green with gold text, which makes the text quite difficult to read, not very aesthetically appealing and the colour scheme looks quite dated.
We would like something fresh and modern, that can still be colourful but doesn't use large blocks of dark colour, and uses the colours within our logo.
Something tying in with the leaves that are used in our logo could work quite nicely, along with the Autumn/Fall colours of soft greens, yellows and reds (also in our existing logo). However also happy to look at fresh, completely out of the box ideas we may not have yet considered.
Target Market(s)
The people that receive this business card work in the aged card or health industry and are either corporate/management level staff or clinical (Registered Nurses, care workers etc.)
Industry/Entity Type
Health Product
Contact Information for Business Card
Company Name - BrindlewayCare
Company locations: United Kingdom, Australia, New Zealand
Staff Details:
Staff name: Derek Mallow
Staff job title: Executive Chairman
Staff email: d.mallow@plumvora.example
Office phone number: 01742 918576
Font styles to use
Other font styles liked:
- Calibri
Requirements
Must have
- Must include the BrindlewayCare brand name in it's current font
- Must include logo (3 leaves in gold circle)
- Must include Business Card Details
Nice to have
- Elements of gold
- White space
- Something autumn themed but not too cliched
Should not have
- No blue - used by a major competitor and we would like to differentiate from them
- Large blocks of dark green colour (the green that appears in our leaves on the logo on our current business card is the background colour and it is far too dark)

```html
<!DOCTYPE html>
<html lang="en">
<head>
<meta charset="utf-8">
<title>BrindlewayCare – Business Card</title>
<link rel="stylesheet" href="https://fonts.googleapis.com/css2?family=Carlito:wght@400;700&display=swap">
<style>
  :root {
    --backdrop: #ebe8e1;
    --card: #ffffff;
    --gold: #a99a70;
    --ink: #5b5b5b;
    --rule: #9a9a9a;
    --berry: #b3195b;
    --ochre: #aaa21b;
    --leaf: #6b8b1f;
    --text-font: "Carlito", "Calibri", Arial, sans-serif;
  }
  * { box-sizing: border-box; margin: 0; padding: 0; }
  html, body {
    width: 1200px;
    height: 950px;
    overflow: hidden;
    background: var(--backdrop);
    font-family: var(--text-font);
  }
  .stage {
    width: 1200px;
    height: 950px;
    display: flex;
    align-items: center;
    justify-content: center;
  }
  .business-card {
    position: relative;
    width: 840px;
    height: 480px;
    background: var(--card);
    border-radius: 26px;
    overflow: hidden;
    box-shadow: 0 10px 30px rgba(0,0,0,0.12);
  }
  .brand {
    position: absolute;
    left: 100px;
    top: 130px;
    display: flex;
    align-items: center;
    gap: 18px;
  }
  .brand-dot {
    width: 22px;
    height: 22px;
    border-radius: 50%;
    background: var(--gold);
    flex: none;
  }
  .brand-name {
    font-size: 58px;
    font-weight: 400;
    color: var(--ink);
    line-height: 1;
  }
  .top-rule {
    position: absolute;
    left: 100px;
    top: 88px;
    width: 690px;
    height: 1px;
    background: var(--rule);
  }
  .locations {
    position: absolute;
    right: 50px;
    top: 100px;
    text-align: right;
    list-style: none;
    font-size: 19px;
    line-height: 1.3;
    color: var(--ink);
  }
  .contact {
    position: absolute;
    left: 100px;
    top: 300px;
    width: 690px;
  }
  .person-line {
    display: flex;
    align-items: center;
    gap: 14px;
  }
  .person-name {
    font-size: 27px;
    font-weight: 700;
    color: var(--gold);
    white-space: nowrap;
  }
  .person-rule {
    flex: 1;
    height: 1px;
    background: var(--rule);
  }
  .person-title {
    font-size: 20px;
    color: var(--ink);
    margin-bottom: 6px;
  }
  .details { list-style: none; }
  .details li {
    display: flex;
    align-items: center;
    gap: 10px;
    font-size: 17px;
    line-height: 1.45;
    color: var(--ink);
  }
  .details svg { width: 14px; height: 14px; flex: none; }
  .accent-strip {
    position: absolute;
    left: 0;
    bottom: 0;
    width: 100%;
    height: 14px;
    display: flex;
  }
  .accent-strip .berry { flex: 0.8; background: var(--berry); }
  .accent-strip .ochre { flex: 1; background: var(--ochre); }
  .accent-strip .leaf { flex: 1.2; background: var(--leaf); }
</style>
</head>
<body>
<main class="stage">
  <article class="business-card">
    <div class="top-rule"></div>

    <div class="brand">
      <span class="brand-dot"></span>
      <p class="brand-name">BrindlewayCare</p>
    </div>

    <ul class="locations">
      <li>United Kingdom</li>
      <li>Australia</li>
      <li>New Zealand</li>
    </ul>

    <section class="contact">
      <div class="person-line">
        <h1 class="person-name">Derek Mallow</h1>
        <span class="person-rule"></span>
      </div>
      <p class="person-title">Executive Chairman</p>
      <ul class="details">
        <li>
          <svg viewBox="0 0 16 16" aria-hidden="true"><path d="M3.5 1.5l2.5 0 1 3.5-1.6 1.2a8 8 0 0 0 4.4 4.4L11 9l3.5 1v2.5c0 1-1 2-2 2A11 11 0 0 1 1.5 3.5c0-1 1-2 2-2z" fill="#5b5b5b"/></svg>
          01742 918576
        </li>
        <li>
          <svg viewBox="0 0 16 16" aria-hidden="true"><rect x="1" y="3" width="14" height="10" rx="1" fill="#5b5b5b"/><path d="M1.5 3.8L8 9l6.5-5.2" stroke="#fff" stroke-width="1.3" fill="none"/></svg>
          d.mallow@plumvora.example
        </li>
        <li>
          <svg viewBox="0 0 16 16" aria-hidden="true"><circle cx="8" cy="8" r="7" fill="#5b5b5b"/><path d="M1 8h14M8 1c-3 3.5-3 10.5 0 14M8 1c3 3.5 3 10.5 0 14" stroke="#fff" stroke-width="1" fill="none"/></svg>
          www.plumvora.example
        </li>
      </ul>
    </section>

    <div class="accent-strip">
      <span class="berry"></span>
      <span class="ochre"></span>
      <span class="leaf"></span>
    </div>
  </article>
</main>
</body>
</html>
```